Family business needs stationery redesign with new logo

Family owned company, established in 1987 wanting a brand 'refresh'. We are an electrical, refrigeration and construction company based in the Barkly Region Northern Territory, Australia. We have a new logo we would like to use which is uploaded along with our current letterhead and email signature. We are also dropping the word 'contractors' so please do not include this on any designs. Please note also, the 'orange' color used in our logo and designs should be Northern Territory red ochre which is as follows:

RGB (Hex): #C75B12
PantoneĀ® 159 C
CMYK: 1 / 74 / 100 / 7

We are needing our stationery redesigned using our new logo. Please include letterheads, business cards, envelopes, and email signatures.

We currently use our business letterheads for quotations, invoices, letters, HR matters, and internal memos.

We also need a separate simplified letterhead for internal paperwork such as employee leave forms, meeting agendas, and meeting minutes etc.

Reason: Needing more submissions of full package designs. We are wanting all our stationery, including business cards, letterheads, email signatures, envelopes, etc to be cohesive. We also require ALL the information, as supplied on our template letterhead, to be included on the new letterhead designs. including electrical license no.etc Thank you, R&W

Reason: needing more time as work has got in the way of looking over designs. A lot of designs not meeting the brief/criteria.

Industry/Entity Type

Business

Colors
0355a3
f37122

Requirements
Must have
• The 'orange' color used in the designs should be Northern Territory red ochre which is as follows:
• RGB (Hex): #C75B12
• PantoneĀ® 159 C
• CMYK: 1 / 74 / 100 / 7
• ***MUST INCLUDE ALL INFORMATION THAT IS ON OUR CURRENT LETTERHEAD***
Should not have
• Please do not include the word 'contractors'

```html
<!DOCTYPE html>
<html lang="en">
<head>
<meta charset="utf-8">
<title>R&amp;W email signature</title>
<link rel="stylesheet" href="https://fonts.googleapis.com/css2?family=Open+Sans:wght@400;600;700&display=swap">
<style>
  :root {
    --ochre: #c95f27;
    --navy: #23336e;
    --paper: #ffffff;
    --on-ochre: #ffffff;
  }
  html, body {
    margin: 0;
    padding: 0;
    overflow: hidden;
  }
  body {
    background: var(--paper);
  }
  .signature {
    position: relative;
    width: 1200px;
    height: 806px;
    background: var(--paper);
    font-family: "Open Sans", sans-serif;
    overflow: hidden;
  }
  .header {
    position: absolute;
    left: 107px;
    top: 232px;
    display: flex;
    align-items: flex-end;
    gap: 14px;
  }
  .person-name {
    font-size: 41px;
    font-weight: 400;
    color: var(--navy);
    line-height: 1;
    letter-spacing: 0.5px;
  }
  .divider {
    width: 1px;
    height: 30px;
    background: var(--ochre);
    opacity: 0.6;
    margin-bottom: 4px;
  }
  .person-title {
    font-size: 15px;
    font-weight: 700;
    color: var(--ochre);
    letter-spacing: 0.8px;
    text-transform: uppercase;
    margin-bottom: 6px;
  }
  .contact-band {
    position: absolute;
    left: 0;
    top: 0;
  }
  .band-shape {
    fill: var(--ochre);
  }
  .contact-list {
    position: absolute;
    left: 106px;
    top: 348px;
    margin: 0;
    padding: 0;
    list-style: none;
    color: var(--on-ochre);
    font-size: 22.5px;
    font-weight: 600;
    line-height: 34.3px;
    white-space: nowrap;
  }
  .brand {
    position: absolute;
    left: 826px;
    top: 400px;
    width: 304px;
    text-align: center;
    color: var(--navy);
    font-weight: 400;
  }
  .brand-name {
    font-size: 48px;
    line-height: 1;
    letter-spacing: 1px;
  }
  .brand-abn {
    margin-top: 58px;
    font-size: 35px;
    line-height: 1;
  }
</style>
</head>
<body>
  <main class="signature">
    <svg class="contact-band" width="1200" height="806" viewBox="0 0 1200 806" aria-hidden="true">
      <polygon class="band-shape" points="70,292 852,292 715,569 70,569"/>
    </svg>

    <div class="header">
      <span class="person-name">DANA</span>
      <span class="divider"></span>
      <span class="person-title">Corporate Services Manager</span>
    </div>

    <ul class="contact-list">
      <li>Address: PO Box 2240, 42 Harlow St, Redgum Creek NT 0870</li>
      <li>Ph: 08 8120</li>
      <li>Cell: 0400</li>
      <li>Email: @rwservices.com.au</li>
      <li>Web: www.rwservices.com.au</li>
    </ul>

    <div class="brand">
      <div class="brand-name">R&amp;W</div>
      <div class="brand-abn">ABN 64</div>
    </div>
  </main>
</body>
</html>
```